Business Card for a Jewellery Brand

Business card for an upscale jewellery brand. Attached is the brand logo and icon and color board. I am looking for two card versions: one for the founder and one is generic. The card should be elegant and convey upscale and premium feel. I am open to both square and rectangle card shapes.

Industry/Entity Type

Jewelry

Contact Information for Business Card

Two cards: (1) Sunela Parvaniya (Founder) (2) General
(1) Sunela Parvaniya card should have Name: Sunela Parvaniya, Title: Founder Email id: sunela@quiremo.com.au. Phone no: +61452913307
(2) Generic card should have Email id: info@quiremo.com.au. Phone no: +61436207518

Requirements
Must have
• Workmark
• ICON
• Phone no
• Email ID
• ABN: 58219740312 (Note: ABN is Business number in Australia)
• Website: www.quiremo.com.au
• Instagram: quiremo_jewellery
• Facebook: @quiremojewellery
Nice to have
• Tagline

```html
<!DOCTYPE html>
<html lang="en">
<head>
<meta charset="utf-8">
<title>Quiremo Business Cards</title>
<link rel="stylesheet" href="https://fonts.googleapis.com/css2?family=Raleway:wght@500;700&family=Source+Sans+3:wght@400&display=swap">
<style>
  :root {
    --stage: #000000;
    --card-light: #f2f2f2;
    --rose: #e69a96;
    --rose-light: #eab0ab;
    --rose-text: #e8948f;
    --ink: #1f1f1f;
    --white: #ffffff;
  }
  * { margin: 0; padding: 0; box-sizing: border-box; }
  html, body { width: 1200px; height: 900px; overflow: hidden; background: var(--stage); }
  .stage { position: relative; width: 1200px; height: 900px; }

  .card { position: absolute; top: 170px; width: 347px; height: 561px; text-align: center; overflow: hidden; }
  .card--front { left: 259px; background: var(--card-light); }
  .card--back { left: 631px; background: var(--rose); }

  .front-mark {
    position: absolute; top: 64px; left: 50%; width: 104px; height: 104px;
    margin-left: -52px; border: 8px solid var(--rose-text); border-radius: 50%;
  }
  .front-wordmark {
    position: absolute; top: 196px; left: 0; width: 100%;
    font-family: "Raleway", sans-serif; font-weight: 700;
    font-size: 34px; letter-spacing: 6px; padding-left: 6px; color: var(--rose-text);
  }
  .person-name {
    position: absolute; top: 338px; left: 0; width: 100%;
    font-family: "Raleway", sans-serif; font-weight: 700;
    font-size: 19px; color: var(--rose-text); letter-spacing: 0.3px;
  }
  .person-title {
    position: absolute; top: 366px; left: 0; width: 100%;
    font-family: "Source Sans 3", sans-serif; font-size: 16px; color: var(--ink);
  }
  .abn {
    position: absolute; top: 396px; left: 0; width: 100%;
    font-family: "Source Sans 3", sans-serif; font-size: 16px; color: var(--ink);
  }
  .abn__label { color: var(--rose-text); }
  .contact-icons {
    position: absolute; top: 446px; left: 0; width: 100%;
    display: flex; justify-content: center; gap: 5px;
  }
  .contact-list {
    position: absolute; top: 461px; left: 0; width: 100%;
    list-style: none;
    font-family: "Source Sans 3", sans-serif; font-size: 16px; line-height: 20.5px; color: var(--ink);
  }

  .back-texture {
    position: absolute; inset: 0;
    background:
      radial-gradient(ellipse 60% 55% at 50% 42%, rgba(255,255,255,0.16), rgba(255,255,255,0) 70%),
      linear-gradient(180deg, var(--rose-light) 0%, var(--rose) 60%, var(--rose) 100%);
  }
  .back-mark {
    position: absolute; top: 182px; left: 50%; width: 100px; height: 100px;
    margin-left: -50px; border: 5px solid var(--white); border-radius: 50%;
  }
  .back-wordmark {
    position: absolute; top: 324px; left: 0; width: 100%;
    font-family: "Raleway", sans-serif; font-weight: 500;
    font-size: 44px; letter-spacing: 8px; padding-left: 8px; color: var(--white);
  }
  .social-icons {
    position: absolute; top: 464px; left: 0; width: 100%;
    display: flex; justify-content: center; gap: 8px;
  }
  .social-dot { width: 25px; height: 25px; border-radius: 50%; background: var(--white); }
  .social-handle {
    position: absolute; top: 492px; left: 0; width: 100%;
    font-family: "Source Sans 3", sans-serif; font-size: 21px; color: var(--white);
  }
</style>
</head>
<body>
<main class="stage">
  <section class="card card--front" aria-label="Founder card">
    <div class="front-mark" aria-hidden="true"></div>
    <div class="front-wordmark">QUIREMO</div>
    <h1 class="person-name">SUNELA PARVANIYA</h1>
    <p class="person-title">Founder</p>
    <p class="abn"><span class="abn__label">ABN:</span> 58219740312</p>
    <div class="contact-icons" aria-hidden="true">
      <svg width="10" height="10" viewBox="0 0 10 10"><path d="M2 0.5 L3.6 2.6 L2.7 3.6 Q4 6 6.4 7.3 L7.4 6.4 L9.5 8 L8.4 9.5 Q3.5 9 0.5 1.6 Z" fill="#e8948f"/></svg>
      <svg width="11" height="10" viewBox="0 0 11 10"><rect x="0.5" y="1.5" width="10" height="7" fill="#e8948f"/><path d="M0.8 1.8 L5.5 5.6 L10.2 1.8" stroke="#f2f2f2" stroke-width="1" fill="none"/></svg>
      <svg width="10" height="10" viewBox="0 0 10 10"><circle cx="5" cy="5" r="4.6" fill="#e8948f"/><path d="M0.6 5 H9.4 M5 0.4 Q2.4 5 5 9.6 M5 0.4 Q7.6 5 5 9.6" stroke="#f2f2f2" stroke-width="0.8" fill="none"/></svg>
    </div>
    <ul class="contact-list">
      <li>+61452913307</li>
      <li>sunela@quiremo.com.au.</li>
      <li>www.quiremo.com.au</li>
    </ul>
  </section>

  <section class="card card--back" aria-label="Brand card">
    <div class="back-texture" role="img" aria-label="Faint large brand emblem pattern in soft rose tones"></div>
    <div class="back-mark" aria-hidden="true"></div>
    <div class="back-wordmark">QUIREMO</div>
    <div class="social-icons" aria-hidden="true">
      <span class="social-dot"></span>
      <span class="social-dot"></span>
    </div>
    <p class="social-handle">@quiremojewellery</p>
  </section>
</main>
</body>
</html>
```